Lumen Fitness Personal Training Business

I need a business card design with a logo for my personal training company. I'd like the colors to be a vibrant green and black. I'd like the logo to incorporate an anvil (or something similar). I train hardcore competitive athletes as well as soccer moms trying to get and/or stay in shape. I need a logo that will not pigeon hole me in one category or the other, but at the same time not be too intimidating to soccer moms, but will not be off putting to the more hardcore trainees. The design should be attention grabbing and aesthetic.
Target Market(s)
Hardcore athletes as well as average people just trying to get/stay in shape.
Industry/Entity Type
Training

```html
<!DOCTYPE html>
<html lang="en">
<head>
<meta charset="utf-8">
<title>Lumen Fitness – Business Card</title>
<link rel="stylesheet" href="https://fonts.googleapis.com/css2?family=Open+Sans:wght@400;600;700&display=swap">
<style>
  :root {
    --green: #06a74e;
    --green-light: #5cbf48;
    --black: #000000;
    --white: #ffffff;
    --backdrop: #d9d9d7;
    --card-w: 700px;
    --card-h: 400px;
  }
  * { box-sizing: border-box; margin: 0; padding: 0; }
  html, body {
    width: 1200px;
    height: 900px;
    overflow: hidden;
    background: var(--backdrop);
    font-family: "Open Sans", Arial, sans-serif;
  }
  .canvas {
    position: relative;
    width: 1200px;
    height: 900px;
  }
  .card {
    position: absolute;
    left: 250px;
    width: var(--card-w);
    height: var(--card-h);
    overflow: hidden;
    box-shadow: 0 6px 18px rgba(0,0,0,0.18);
  }

  /* Front */
  .card--front { top: 30px; background: var(--black); }
  .front-band {
    position: absolute;
    left: 0;
    width: 100%;
    background: var(--green);
  }
  .front-band--top { top: 0; height: 72px; }
  .front-band--bottom { bottom: 0; height: 56px; }
  .brand {
    position: absolute;
    display: flex;
    align-items: center;
    gap: 18px;
  }
  .brand__dot {
    width: 34px;
    height: 34px;
    border-radius: 50%;
  }
  .brand__name {
    font-weight: 600;
    font-size: 44px;
    letter-spacing: 3px;
    line-height: 1;
    white-space: nowrap;
  }
  .card--front .brand {
    top: 152px;
    left: 0;
    width: 100%;
    justify-content: center;
  }
  .card--front .brand__dot { background: var(--white); }
  .card--front .brand__name { color: var(--white); }

  /* Back */
  .card--back { top: 470px; background: var(--green); }
  .back-header {
    position: absolute;
    top: 0; left: 0;
    width: 100%;
    height: 140px;
    background: var(--black);
  }
  .back-logo-block {
    position: absolute;
    top: 0; right: 0;
    width: 380px;
    height: 236px;
    background: var(--black);
  }
  .card--back .brand {
    top: 70px;
    left: 360px;
    width: 320px;
    justify-content: center;
    gap: 12px;
  }
  .card--back .brand__dot { width: 24px; height: 24px; background: var(--green); }
  .card--back .brand__name { color: var(--green); font-size: 30px; letter-spacing: 2px; }

  .holder {
    position: absolute;
    top: 150px;
    left: 40px;
    color: var(--white);
  }
  .holder__name { font-weight: 700; font-size: 26px; line-height: 1.15; }
  .holder__title { font-weight: 400; font-size: 15px; }

  .contact-list {
    position: absolute;
    right: 30px;
    top: 252px;
    list-style: none;
    color: var(--white);
    font-size: 17px;
    line-height: 23px;
    text-align: right;
  }
  .contact-list li {
    display: flex;
    justify-content: flex-end;
    align-items: center;
    gap: 10px;
  }
  .contact-list svg { width: 14px; height: 14px; flex: none; fill: var(--white); }
  .back-strip {
    position: absolute;
    bottom: 0; left: 0;
    width: 100%;
    height: 20px;
    background: var(--green-light);
  }
</style>
</head>
<body>
<main class="canvas">

  <section class="card card--front" aria-label="Business card front">
    <div class="front-band front-band--top"></div>
    <div class="front-band front-band--bottom"></div>
    <div class="brand">
      <span class="brand__dot"></span>
      <span class="brand__name">LUMEN FITNESS</span>
    </div>
  </section>

  <section class="card card--back" aria-label="Business card back">
    <div class="back-header"></div>
    <div class="back-logo-block"></div>
    <div class="brand">
      <span class="brand__dot"></span>
      <span class="brand__name">LUMEN FITNESS</span>
    </div>

    <div class="holder">
      <p class="holder__name">Daniel Reyes</p>
      <p class="holder__title">Managing Director</p>
    </div>

    <ul class="contact-list">
      <li>123.456.7890
        <svg viewBox="0 0 16 16" aria-hidden="true"><path d="M2 5c0-2 3-3 6-3s6 1 6 3v1h-3V5H5v1H2z M4 7h8l2 6H2z"/></svg>
      </li>
      <li>123.456.7890
        <svg viewBox="0 0 16 16" aria-hidden="true"><path d="M4 1h8v14H4z M5 3v8h6V3z"/></svg>
      </li>
      <li>info@youremail.com
        <svg viewBox="0 0 16 16" aria-hidden="true"><path d="M1 3h14v10H1z M2 4l6 5 6-5v-.5H2z" fill-rule="evenodd"/></svg>
      </li>
      <li>www.website.com
        <svg viewBox="0 0 16 16" aria-hidden="true"><path d="M6 10l4-4 1 1-4 4z M3 9l3-3 1.5 1.5L5 10l1 1 2.5-2.5L10 10l-3 3a2.5 2.5 0 0 1-4-4z M13 7l-3 3-1.5-1.5L11 6l-1-1-2.5 2.5L6 6l3-3a2.5 2.5 0 0 1 4 4z"/></svg>
      </li>
      <li>1234, Address Goes Here, Country Name, 123456
        <svg viewBox="0 0 16 16" aria-hidden="true"><path d="M8 1a5 5 0 0 1 5 5c0 4-5 9-5 9S3 10 3 6a5 5 0 0 1 5-5z M8 4a2 2 0 1 0 0 4 2 2 0 0 0 0-4z" fill-rule="evenodd"/></svg>
      </li>
    </ul>

    <div class="back-strip"></div>
  </section>

</main>
</body>
</html>
```